We are a recruitment company based in Norwich/Cambridge England.
I have included our company logo which we want to remain the same.

What we are looking for is a new creative Business card which will really stand out!!

Contact Information for Business Card

Harriet Dunmore
email: Harriet@plavex.co.uk
Address: Brackwell House
Fenmoor Enterprise Park
Partridge Way
Norwich
QB9 3KX
Tel:01632 960418

```html
<!DOCTYPE html>
<html lang="en">
<head>
<meta charset="utf-8">
<title>Plavex Business Card</title>
<link href="https://fonts.googleapis.com/css2?family=Roboto:wght@400;500;700&display=swap" rel="stylesheet">
<style>
  :root {
    --backdrop: #d9d4cc;
    --card-frost: #eef0ee;
    --card-frost-edge: #dfe3e0;
    --brand-green: #5aa82a;
    --green-deep: #4f9a22;
    --green-light: #7cc242;
    --shadow-grey: #6e7072;
    --text-grey: #6b6d6f;
    --text-white: #f4f8f0;
    --address-green: #9fd46f;
  }
  * { margin: 0; padding: 0; box-sizing: border-box; }
  html, body {
    width: 1200px;
    height: 969px;
    overflow: hidden;
    background: var(--backdrop);
    font-family: "Roboto", Arial, sans-serif;
  }
  .business-card {
    position: absolute;
    left: 100px;
    top: 200px;
    width: 1000px;
    height: 570px;
    background: linear-gradient(160deg, var(--card-frost), var(--card-frost-edge));
    box-shadow: 0 10px 30px rgba(0,0,0,0.15);
    overflow: hidden;
  }
  .card-shapes {
    position: absolute;
    inset: 0;
  }
  .brand {
    position: absolute;
    left: 70px;
    top: 90px;
    display: flex;
    align-items: center;
    gap: 22px;
  }
  .brand-dot {
    width: 70px;
    height: 70px;
    border-radius: 50%;
    background: var(--brand-green);
  }
  .brand-name {
    font-size: 72px;
    font-weight: 500;
    color: var(--brand-green);
    line-height: 1;
  }
  .brand-tagline {
    position: absolute;
    left: 162px;
    top: 172px;
    font-size: 15px;
    letter-spacing: 2.6px;
    color: var(--text-grey);
  }
  .person {
    position: absolute;
    right: 35px;
    top: 305px;
    text-align: right;
    font-weight: 700;
    color: var(--text-white);
  }
  .person-name { font-size: 31px; letter-spacing: 1px; }
  .person-role { font-size: 24px; letter-spacing: 1px; margin-top: 6px; }
  .contact-list {
    position: absolute;
    right: 28px;
    top: 410px;
    list-style: none;
    color: var(--text-white);
    font-size: 23px;
  }
  .contact-list li {
    display: flex;
    align-items: center;
    justify-content: flex-end;
    gap: 14px;
    height: 33px;
  }
  .contact-icon { width: 22px; height: 22px; fill: var(--text-white); }
  .divider {
    position: absolute;
    left: 693px;
    top: 418px;
    width: 1px;
    height: 125px;
    background: rgba(255,255,255,0.45);
  }
  .address {
    position: absolute;
    right: 328px;
    top: 450px;
    text-align: right;
    color: var(--address-green);
    font-size: 23px;
    line-height: 32px;
  }
  .address .web { letter-spacing: 3px; }
</style>
</head>
<body>
  <div class="business-card">
    <svg class="card-shapes" width="1000" height="570" viewBox="0 0 1000 570">
      <path class="cloud-shadow" fill="var(--shadow-grey)"
        d="M302 570 C350 420 425 312 520 302 C570 298 615 310 640 320 C655 210 740 98 870 96 L1000 96 L1000 570 Z"/>
      <defs>
        <linearGradient id="cloudGreen" x1="0" y1="1" x2="1" y2="0">
          <stop offset="0" stop-color="var(--green-deep)"/>
          <stop offset="1" stop-color="var(--green-light)"/>
        </linearGradient>
      </defs>
      <path class="cloud-band" fill="url(#cloudGreen)"
        d="M353 570 C400 425 470 322 560 314 C610 310 648 322 670 332 C684 222 762 112 882 108 L1000 108 L1000 570 Z"/>
    </svg>

    <div class="brand">
      <span class="brand-dot"></span>
      <span class="brand-name">Plavex</span>
    </div>
    <p class="brand-tagline">Technology Recruitment</p>

    <div class="person">
      <p class="person-name">TOBIAS RENWICK</p>
      <p class="person-role">CEO/FOUNDER</p>
    </div>

    <div class="divider"></div>

    <div class="address">
      <p>4120 Larkspur Lane</p>
      <p>Elmhurst, Vale 34590</p>
      <p class="web">www.plavex.com</p>
    </div>

    <ul class="contact-list">
      <li>689 555 0147
        <svg class="contact-icon" viewBox="0 0 24 24" aria-hidden="true"><path d="M6.6 10.8a15 15 0 0 0 6.6 6.6l2.2-2.2a1 1 0 0 1 1-.25 11.4 11.4 0 0 0 3.6.57 1 1 0 0 1 1 1V20a1 1 0 0 1-1 1A17 17 0 0 1 3 4a1 1 0 0 1 1-1h3.5a1 1 0 0 1 1 1c0 1.25.2 2.45.57 3.57a1 1 0 0 1-.25 1z"/></svg>
      </li>
      <li>836 555 0192
        <svg class="contact-icon" viewBox="0 0 24 24" aria-hidden="true"><path d="M7 1h10a2 2 0 0 1 2 2v18a2 2 0 0 1-2 2H7a2 2 0 0 1-2-2V3a2 2 0 0 1 2-2zm0 3v14h10V4zm5 15.5a1.2 1.2 0 1 0 0 2.4 1.2 1.2 0 0 0 0-2.4z"/></svg>
      </li>
      <li>482 555 0163
        <svg class="contact-icon" viewBox="0 0 24 24" aria-hidden="true"><path d="M7 2h10v6H7zM4 9h16a2 2 0 0 1 2 2v9H2v-9a2 2 0 0 1 2-2zm3 9h10v-4H7z"/></svg>
      </li>
      <li>tobias@plavex.com
        <svg class="contact-icon" viewBox="0 0 24 24" aria-hidden="true"><path d="M2 5h20v14H2zm2 2v.5l8 5 8-5V7zm0 2.8V17h16V9.8l-8 5z"/></svg>
      </li>
    </ul>
  </div>
</body>
</html>
```